New Business Card Design

We would like to refresh our business cards and make them look better. We are an IT company specialising in Cloud Services, IT Managed Services, software and hardware. I have attached a PSD of our current design. Also attached our logo.
Updates

I have uploaded all new logos in EPS format.

Can you please edit all designs to include a job title for Marcus Hollis, eg. General Manager

Industry/Entity Type

Software

Colors
ffffff

Requirements
Must have
• Please use white background.
Should not have
• Black background

```html
<!DOCTYPE html>
<html lang="en">
<head>
<meta charset="utf-8">
<title>Meridian Technology – Business Card</title>
<link href="https://fonts.googleapis.com/css2?family=Open+Sans:wght@400;600;700&display=swap" rel="stylesheet">
<style>
  :root {
    --canvas: #e9e7e3;
    --card-top: #ffffff;
    --card-bottom: #e4e5e7;
    --slate: #7f8a97;
    --accent-red: #c8362b;
    --ink: #3a3d42;
    --ink-soft: #55595f;
    --white: #ffffff;
  }
  * { box-sizing: border-box; margin: 0; padding: 0; }
  html, body {
    width: 1200px; height: 720px; overflow: hidden;
    background: var(--canvas);
    font-family: "Open Sans", Arial, sans-serif;
  }
  .stage { position: relative; width: 1200px; height: 720px; }
  .card {
    position: absolute; top: 195px;
    width: 540px; height: 330px;
    background: linear-gradient(160deg, var(--card-top) 0%, var(--card-bottom) 100%);
    box-shadow: 0 2px 10px rgba(0,0,0,0.12);
    overflow: hidden;
  }
  .card--front { left: 40px; }
  .card--back { left: 620px; }

  .band { position: absolute; inset: 0; width: 540px; height: 330px; }

  .brand {
    position: absolute; display: flex; align-items: center; gap: 10px;
  }
  .brand__mark {
    width: 14px; height: 14px; background: var(--slate); flex: none;
  }
  .brand__name {
    font-weight: 400; color: var(--ink);
    font-size: 24px; line-height: 1; white-space: nowrap;
  }
  .card--front .brand { left: 36px; top: 120px; }

  .holder { position: absolute; right: 26px; top: 18px; text-align: right; }
  .holder__name { color: var(--accent-red); font-weight: 700; font-size: 17px; }
  .holder__title { color: var(--ink); font-size: 12px; margin-top: 1px; }

  .contacts {
    position: absolute; right: 22px; top: 130px;
    list-style: none; text-align: right;
  }
  .contacts li {
    display: flex; justify-content: flex-end; align-items: center; gap: 7px;
    color: var(--white); font-size: 13.5px; line-height: 25px;
  }
  .contacts svg { width: 13px; height: 13px; flex: none; }

  .card--back .brand { left: 0; right: 0; justify-content: center; top: 110px; }
  .card--back .brand__name { font-size: 26px; }

  .tagline {
    position: absolute; left: 0; right: 0; top: 195px;
    text-align: center; color: var(--ink);
    font-size: 16.5px; line-height: 24px;
  }
  .web {
    position: absolute; left: 0; right: 0; top: 268px;
    text-align: center; color: var(--ink-soft);
    font-size: 14px; letter-spacing: 2px;
  }
  .web__domain { color: var(--accent-red); font-weight: 600; }
</style>
</head>
<body>
<main class="stage">

  <section class="card card--front" aria-label="Business card front">
    <svg class="band" viewBox="0 0 540 330" aria-hidden="true">
      <path d="M0,320 L0,290 C200,285 250,110 540,112 L540,330 Z" fill="var(--slate)"/>
      <path d="M0,284 C200,279 250,104 540,106" fill="none" stroke="var(--accent-red)" stroke-width="4"/>
    </svg>

    <div class="brand">
      <span class="brand__mark"></span>
      <span class="brand__name">Meridian Technology</span>
    </div>

    <div class="holder">
      <p class="holder__name">Marcus Hollis</p>
      <p class="holder__title">General Manager</p>
    </div>

    <ul class="contacts">
      <li>
        <svg viewBox="0 0 16 16" aria-hidden="true"><circle cx="8" cy="8" r="7.5" fill="none" stroke="#fff" stroke-width="1.2"/><path d="M5 4.5l1.6-.4 1 2-1 .8a5 5 0 0 0 2.5 2.5l.8-1 2 1-.4 1.6c-3.5.2-6.7-3-6.5-6.5z" fill="#fff"/></svg>
        07 3555 0142
      </li>
      <li>
        <svg viewBox="0 0 16 16" aria-hidden="true"><rect x="4.5" y="1.5" width="7" height="13" rx="1.2" fill="#fff"/><rect x="5.7" y="3" width="4.6" height="7.5" fill="var(--slate)"/></svg>
        0400 555 219
      </li>
      <li>
        <svg viewBox="0 0 16 16" aria-hidden="true"><rect x="1.5" y="3.5" width="13" height="9" rx="1" fill="#fff"/><path d="M1.8 4l6.2 5 6.2-5" fill="none" stroke="var(--slate)" stroke-width="1.2"/></svg>
        m.hollis@meridianit.com.au
      </li>
      <li>
        <svg viewBox="0 0 16 16" aria-hidden="true"><circle cx="8" cy="8" r="6.5" fill="none" stroke="#fff" stroke-width="1.3"/><ellipse cx="8" cy="8" rx="2.8" ry="6.5" fill="none" stroke="#fff" stroke-width="1.1"/><path d="M1.5 8h13" stroke="#fff" stroke-width="1.1"/></svg>
        www.meridianit.com.au
      </li>
    </ul>
  </section>

  <section class="card card--back" aria-label="Business card back">
    <div class="brand">
      <span class="brand__mark"></span>
      <span class="brand__name">Meridian Technology</span>
    </div>

    <p class="tagline">We are an IT company specializing in Cloud Services<br>IT Managed Services, software and hardware</p>

    <p class="web">www.<span class="web__domain">meridianit</span>.com.au</p>
  </section>

</main>
</body>
</html>
```